Coastline Premier Retreats Business Card Design

Design a business card for Coastline Premier Retreats. Look at the website for colors and reference. Card should have logo, name, title, office number, mobile number, email, URL and a tagline like, "Luxury Hotel & Resort Email Marketing" (This might change).

https://www.coastlinepremierretreats.example

The rest I will leave up to your imagination.

Contact Information for Business Card

Logo, name, title, office number, mobile number, email, URL and a tagline like, "Luxury Hotel & Resort Email Marketing" (This might change).

```html
<!DOCTYPE html>
<html lang="en">
<head>
<meta charset="utf-8">
<title>Coastline Premier Retreats – Business Card</title>
<link rel="stylesheet" href="https://fonts.googleapis.com/css2?family=Open+Sans:wght@400;600;700&display=swap">
<style>
  :root {
    --backdrop: #dedfe2;
    --card-dark: #212125;
    --brand-orange: #f47421;
    --brand-orange-deep: #d9611a;
    --text-light: #ffffff;
    --divider: #8a8a90;
  }
  * { box-sizing: border-box; margin: 0; padding: 0; }
  html, body {
    width: 1200px; height: 780px; overflow: hidden;
    background: var(--backdrop);
    font-family: "Open Sans", Arial, sans-serif;
  }
  .sheet {
    position: relative; width: 1200px; height: 780px;
    display: flex; align-items: center; justify-content: center; gap: 40px;
  }
  .card {
    position: relative; width: 540px; height: 310px; overflow: hidden;
    box-shadow: 0 10px 24px rgba(0,0,0,.22);
  }
  /* Front */
  .card-front { background: var(--card-dark); }
  .front-brand {
    position: absolute; left: 34px; top: 108px; width: 220px;
    display: flex; align-items: center; gap: 10px;
  }
  .brand-mark { width: 14px; height: 14px; background: var(--brand-orange); flex: none; }
  .brand-name {
    color: var(--text-light); font-weight: 700; font-size: 19px; line-height: 1.15;
  }
  .front-divider {
    position: absolute; left: 272px; top: 28px; width: 1px; height: 160px;
    background: var(--divider);
  }
  .contact-block { position: absolute; left: 296px; top: 34px; color: var(--text-light); }
  .person-name { font-size: 25px; font-weight: 700; line-height: 1.1; }
  .person-name .given { color: var(--brand-orange); }
  .person-title { font-size: 13px; margin-top: 3px; }
  .contact-list { list-style: none; margin-top: 12px; font-size: 10.5px; }
  .contact-list li { display: flex; align-items: center; gap: 8px; height: 17px; }
  .contact-list svg { width: 11px; height: 11px; flex: none; fill: var(--brand-orange); }
  .tagline-band {
    position: absolute; left: 0; right: 0; bottom: 26px; height: 34px;
    background: var(--brand-orange); color: var(--text-light);
    display: flex; align-items: center; justify-content: flex-end; padding-right: 40px;
    font-size: 13px; font-weight: 600;
  }
  /* Back */
  .card-back { background: var(--brand-orange); display: flex; align-items: center; justify-content: center; }
  .back-brand {
    color: var(--brand-orange-deep); font-weight: 700; font-size: 36px; letter-spacing: .5px;
    text-align: center; line-height: 1.15;
  }
</style>
</head>
<body>
<main class="sheet">
  <section class="card card-front" aria-label="Business card front">
    <div class="front-brand">
      <span class="brand-mark"></span>
      <span class="brand-name">Coastline Premier Retreats</span>
    </div>
    <div class="front-divider"></div>
    <div class="contact-block">
      <h1 class="person-name"><span class="given">Lena</span> Marvell</h1>
      <p class="person-title">Co-Founder</p>
      <ul class="contact-list">
        <li><svg viewBox="0 0 24 24"><path d="M6.6 10.8a15 15 0 0 0 6.6 6.6l2.2-2.2a1 1 0 0 1 1-.25 11.4 11.4 0 0 0 3.6.57 1 1 0 0 1 1 1V20a1 1 0 0 1-1 1A17 17 0 0 1 3 4a1 1 0 0 1 1-1h3.5a1 1 0 0 1 1 1 11.4 11.4 0 0 0 .57 3.6 1 1 0 0 1-.25 1z"/></svg>(555) 014-2758</li>
        <li><svg viewBox="0 0 24 24"><path d="M7 1h10a2 2 0 0 1 2 2v18a2 2 0 0 1-2 2H7a2 2 0 0 1-2-2V3a2 2 0 0 1 2-2zm0 3v14h10V4z"/></svg>(555) 019-7777</li>
        <li><svg viewBox="0 0 24 24"><path d="M12 2a10 10 0 1 0 0 20 10 10 0 0 0 0-20zm6.9 6h-3a15 15 0 0 0-1.4-3.6A8 8 0 0 1 18.9 8zM12 4a13 13 0 0 1 1.9 4h-3.8A13 13 0 0 1 12 4zM4.3 14a8 8 0 0 1 0-4h3.4a16 16 0 0 0 0 4zm.8 2h3a15 15 0 0 0 1.4 3.6A8 8 0 0 1 5.1 16zm3-8h-3a8 8 0 0 1 4.4-3.6A15 15 0 0 0 8.1 8zM12 20a13 13 0 0 1-1.9-4h3.8A13 13 0 0 1 12 20zm2.3-6H9.7a14 14 0 0 1 0-4h4.6a14 14 0 0 1 0 4zm.2 5.6a15 15 0 0 0 1.4-3.6h3a8 8 0 0 1-4.4 3.6zm1.8-5.6a16 16 0 0 0 0-4h3.4a8 8 0 0 1 0 4z"/></svg>www.coastlinepremierretreats.example</li>
        <li><svg viewBox="0 0 24 24"><path d="M3 5h18a1 1 0 0 1 1 1v12a1 1 0 0 1-1 1H3a1 1 0 0 1-1-1V6a1 1 0 0 1 1-1zm9 7.5L4.5 7.5v.1L12 14l7.5-6.4v-.1z"/></svg>info@coastlinepremierretreats.example</li>
      </ul>
    </div>
    <div class="tagline-band">Luxury Hotel &amp; Resort Email Marketing</div>
  </section>

  <section class="card card-back" aria-label="Business card back">
    <p class="back-brand">Coastline Premier<br>Retreats</p>
  </section>
</main>
</body>
</html>
```